Moravel Aesthetic Doctor

I require an elegant, luxurious looking business card for my aesthetic business. I am a doctor and that will set me aside from competitors. I am planning to provide home and spa based treatments to clients with high expectations. I have attached my logo.

```html
<!DOCTYPE html>
<html lang="en">
<head>
<meta charset="utf-8">
<title>Moravel Aesthetic Doctor – Business Card</title>
<link href="https://fonts.googleapis.com/css2?family=Open+Sans:wght@300;400&display=swap" rel="stylesheet">
<style>
  :root {
    --page: #ecebe8;
    --white: #ffffff;
    --paper-shade: #ececec;
    --blue: #1f78c1;
    --blue-deep: #1766ad;
    --blue-mid: #3a9fd8;
    --blue-light: #8ccdf0;
    --grey-text: #555a60;
    --accent: #1aa3e0;
  }
  * { margin: 0; padding: 0; box-sizing: border-box; }
  html, body {
    width: 1200px; height: 1136px; overflow: hidden;
    background: var(--page);
    font-family: "Open Sans", Arial, sans-serif;
  }
  .canvas { position: relative; width: 1200px; height: 1136px; }
  .card {
    position: absolute; left: 160px; width: 880px; height: 503px;
    overflow: hidden; border-radius: 4px;
    box-shadow: 0 14px 30px rgba(0,0,0,0.22);
  }
  .card--front { top: 46px; background: linear-gradient(135deg, var(--white) 40%, var(--paper-shade)); }
  .card--back { top: 588px; background: radial-gradient(ellipse at 55% 45%, var(--blue) 0%, var(--blue-deep) 100%); }
  .wave { position: absolute; inset: 0; width: 100%; height: 100%; }

  .brand { position: absolute; display: flex; align-items: center; }
  .brand__dot { border-radius: 50%; flex: none; }
  .brand__name { font-weight: 300; line-height: 1.1; text-transform: uppercase; white-space: nowrap; }
  .card--front .brand { left: 56px; top: 156px; gap: 18px; }
  .card--front .brand__dot { width: 76px; height: 76px; border: 2px solid #b9bcc0; }
  .card--front .brand__name { color: var(--grey-text); font-size: 22px; letter-spacing: 2px; }

  .services { position: absolute; left: 120px; top: 300px; list-style: none; color: var(--grey-text); font-size: 19px; line-height: 1.55; }
  .services li::before {
    content: ""; display: inline-block; width: 8px; height: 8px; border-radius: 50%;
    background: var(--accent); margin-right: 14px; vertical-align: middle;
  }
  .social { position: absolute; left: 120px; top: 456px; display: flex; gap: 10px; }
  .social span { width: 16px; height: 16px; border-radius: 50%; background: var(--accent); }

  .contact { position: absolute; right: 56px; top: 70px; width: 290px; color: var(--white); text-align: center; }
  .contact__name { font-size: 26px; font-weight: 400; }
  .contact__cred { font-size: 12px; color: var(--blue-light); letter-spacing: 1px; margin-bottom: 14px; }
  .contact__qual { font-size: 15px; font-weight: 300; line-height: 1.5; margin-bottom: 26px; }
  .contact__line { font-size: 16px; font-weight: 300; line-height: 1.9; display: flex; align-items: center; justify-content: center; gap: 10px; }
  .contact__line svg { width: 14px; height: 14px; fill: var(--blue-light); }

  .card--back .brand { left: 210px; top: 160px; gap: 26px; }
  .card--back .brand__dot { width: 110px; height: 110px; border: 3px solid var(--white); }
  .card--back .brand__name { color: var(--white); font-size: 40px; letter-spacing: 3px; }
  .tagline { position: absolute; left: 0; right: 0; top: 350px; text-align: center; color: var(--white); font-size: 20px; font-weight: 300; letter-spacing: 1px; }
</style>
</head>
<body>
<main class="canvas">
  <section class="card card--front" aria-label="Card front">
    <svg class="wave" viewBox="0 0 880 503" preserveAspectRatio="none" aria-hidden="true">
      <path d="M500 0 C360 130 610 310 520 503 L880 503 L880 0 Z" fill="var(--blue-light)"/>
      <path d="M515 0 C380 130 625 310 540 503 L880 503 L880 0 Z" fill="var(--blue-mid)"/>
      <path d="M530 0 C395 130 640 310 556 503" fill="none" stroke="var(--white)" stroke-width="2"/>
      <path d="M545 0 C410 130 655 310 572 503 L880 503 L880 0 Z" fill="var(--blue)"/>
    </svg>

    <div class="brand">
      <span class="brand__dot"></span>
      <p class="brand__name">Moravel<br>Aesthetic Doctor</p>
    </div>

    <ul class="services">
      <li>Dermal injectables</li>
      <li>Plasma facials</li>
      <li>Microneedling</li>
      <li>Skin boosters</li>
      <li>Excessive sweating</li>
    </ul>
    <div class="social" aria-label="Social links"><span></span><span></span></div>

    <div class="contact">
      <p class="contact__name">Dr Elsa Marwick</p>
      <p class="contact__cred">MRCPCH MD</p>
      <p class="contact__qual">Australasian Diploma of<br>Aesthetic Medicine</p>
      <p class="contact__line">0800 555 014
        <svg viewBox="0 0 24 24"><path d="M6.6 10.8a15 15 0 0 0 6.6 6.6l2.2-2.2c.3-.3.7-.4 1-.2 1.1.4 2.3.6 3.6.6.6 0 1 .4 1 1V20c0 .6-.4 1-1 1C10.6 21 3 13.4 3 4c0-.6.4-1 1-1h3.5c.6 0 1 .4 1 1 0 1.3.2 2.5.6 3.6.1.3 0 .7-.2 1z"/></svg></p>
      <p class="contact__line">elsa@moravel.co.nz
        <svg viewBox="0 0 24 24"><path d="M2 5h20v14H2z M2 5l10 8 10-8" fill="none" stroke="var(--blue-light)" stroke-width="2"/></svg></p>
      <p class="contact__line">www.moravel.co.nz
        <svg viewBox="0 0 24 24"><circle cx="12" cy="12" r="9" fill="none" stroke="var(--blue-light)" stroke-width="2"/><path d="M3 12h18M12 3c3 3 3 15 0 18M12 3c-3 3-3 15 0 18" fill="none" stroke="var(--blue-light)" stroke-width="1.5"/></svg></p>
    </div>
  </section>

  <section class="card card--back" aria-label="Card back">
    <div class="brand">
      <span class="brand__dot"></span>
      <p class="brand__name">Moravel<br>Aesthetic Doctor</p>
    </div>
    <p class="tagline">Home and Spa Based Treatments</p>
  </section>
</main>
</body>
</html>
```